Kestrada LLC, needs a web page no more than 5 pages (for now)

Kestrada is a general contractor. Our services include general contracting, design-build construction, disaster recovery and environmental remediation. Our main clients are PMX, TQ, State and Local Gov't Agencies, Hospitals and Schools. Kestrada is also a SDVOSB.

```html
<!DOCTYPE html>
<html lang="en">
<head>
<meta charset="utf-8">
<title>Kestrada LLC</title>
<link href="https://fonts.googleapis.com/css2?family=Poppins:wght@300;400;500;600;700;800&display=swap" rel="stylesheet">
<style>
:root{
  --gold:#c8923a;
  --gold-light:#e2b458;
  --gold-dark:#a8742a;
  --ink:#1b1b1b;
  --text:#3c3c3c;
  --muted:#8a8a8a;
  --line:#d9d9d9;
  --white:#ffffff;
  --cream:#fdf8f1;
  --blue:#1d4fd6;
  --footer:#0b0b0b;
}
*{box-sizing:border-box;margin:0;padding:0}
html,body{width:1200px;height:5017px;overflow:hidden}
body{font-family:"Poppins",sans-serif;color:var(--text);background:var(--white);position:relative}
.abs{position:absolute}
.btn{position:absolute;display:flex;align-items:center;justify-content:center;font-weight:600;font-size:13px;letter-spacing:.5px;color:var(--white);background:linear-gradient(90deg,var(--gold-dark),var(--gold-light));border-radius:4px;box-shadow:0 4px 10px rgba(0,0,0,.2)}
.sec-title{position:absolute;left:0;width:1200px;text-align:center;font-size:38px;font-weight:300;color:var(--ink);letter-spacing:-.5px}
.sec-title b{font-weight:800}
.rule{position:absolute;height:3px;width:95px;background:linear-gradient(90deg,var(--gold-dark),var(--gold-light))}

/* hero */
.hero{left:0;top:0;width:1200px;height:790px;background:linear-gradient(115deg,#0d1422 0%,#1f2a3d 35%,#6a5232 60%,#e2a543 80%,#f4d18a 100%)}
.logo{position:absolute;display:flex;align-items:center;gap:8px;font-weight:500;color:var(--white)}
.logo .mark{width:30px;height:30px;border:2px solid var(--gold-light);border-radius:50%}
.logo span{font-size:26px;letter-spacing:1px}
.nav{left:366px;top:50px;display:flex;gap:30px;font-size:13px;font-weight:500;color:var(--white)}
.nav .active{color:var(--gold-light)}
.hero h1{left:110px;top:185px;font-size:39px;line-height:49px;font-weight:400;color:var(--white)}
.hero h1 b{display:block;font-weight:800;color:var(--gold-light)}
.hero p{left:110px;top:340px;width:370px;font-size:15.5px;line-height:27px;color:var(--white)}
.dots{display:flex;gap:6px}
.dots i{width:10px;height:10px;border-radius:50%;border:1.5px solid #bbb;display:block}
.dots i.on{background:var(--gold);border-color:var(--gold)}

/* about */
.about-photo{left:0;top:640px;width:640px;height:755px;background:linear-gradient(90deg,#6d7f96 0%,#a9b6c6 55%,rgba(255,255,255,0) 100%)}
.about h2{left:612px;top:850px;font-size:40px;font-weight:300;color:var(--ink)}
.about h2 b{font-weight:800;color:var(--gold)}
.about p{left:612px;width:480px;font-size:15.5px;line-height:27px;color:var(--text)}
.about p strong{color:var(--gold-dark)}

/* services */
.services{left:0;top:1395px;width:1200px;height:700px;background:linear-gradient(180deg,#d7a650 0%,#d4a455 60%,#c79545 100%)}
.services .sec-title{color:var(--white)}
.services .sec-title b{color:var(--ink)}
.card{position:absolute;top:205px;width:230px;text-align:center;border-radius:6px}
.card .ph{height:235px;border-radius:4px}
.card h3{font-size:19px;font-weight:500;color:var(--ink);margin-top:14px;letter-spacing:-.4px}
.card p{font-size:11.5px;line-height:18px;color:#6b5330;margin:6px 6px 0}
.card.hover{background:rgba(255,255,255,.28);height:385px}
.card .more{display:flex;justify-content:center;gap:10px;font-size:9.5px;font-weight:600;color:var(--ink);margin-top:14px}

/* clients */
.client{position:absolute;top:2300px;width:280px;height:260px;text-align:center}
.client .name{position:absolute;top:205px;width:100%;font-size:13px;font-weight:500;color:var(--ink)}
.seal{position:absolute;border-radius:50%;border:3px solid var(--gold)}
.divider{position:absolute;top:2300px;width:1px;height:260px;background:var(--line)}

/* events */
.events{left:0;top:2650px;width:1200px;height:780px;background:linear-gradient(180deg,#b98a4c 0%,#a97c45 50%,#b88a4a 100%)}
.events .sec-title{color:var(--white)}
.event-main{left:112px;top:195px;width:470px;height:410px;border-radius:6px;background:linear-gradient(160deg,#8fb4c9 0%,#4c8a5a 50%,#d6c3a0 100%)}
.event-cap{position:absolute;left:0;right:0;bottom:0;height:115px;background:rgba(255,255,255,.9);border-radius:0 0 6px 6px;padding:20px 40px}
.event-cap h3{font-size:20px;font-weight:600;color:var(--ink)}
.event-cap p{font-size:14px;line-height:20px;color:#555;margin-top:6px}
.event-sm{position:absolute;left:617px;width:470px;height:193px;background:var(--white);border-radius:6px;overflow:hidden}
.event-sm .ph{position:absolute;left:0;top:0;width:215px;height:100%}
.event-sm .body{position:absolute;left:228px;top:18px;width:225px}
.badge{display:inline-block;background:var(--blue);color:var(--white);font-size:9px;font-weight:600;padding:8px 10px}
.event-sm h4{font-size:15px;line-height:19px;font-weight:600;color:var(--ink);margin-top:16px}
.event-sm p{font-size:9.5px;line-height:16px;color:#777;margin-top:8px}
.btn-outline{position:absolute;left:518px;top:648px;width:163px;height:45px;border:1.5px solid var(--white);border-radius:3px;color:var(--white);font-size:13px;font-weight:600;display:flex;align-items:center;justify-content:center}

/* testimonials */
.testi{left:0;top:3430px;width:1200px;height:540px;background:var(--cream)}
.testi .sec-title{color:var(--gold);font-weight:800}
.t-card{position:absolute;top:180px;height:225px;background:var(--white);border-radius:12px;box-shadow:0 6px 18px rgba(0,0,0,.12)}
.quote{position:absolute;font-size:80px;font-weight:700;color:#e6c787;line-height:1}
.t-main h3{text-align:center;margin-top:24px;font-size:21px;font-weight:500;color:var(--gold)}
.t-main .role{text-align:center;font-size:14px;color:#555}
.t-main p{text-align:center;font-size:13.5px;line-height:23px;font-style:italic;color:#555;width:610px;margin:22px auto 0}

/* contact */
.contact h2{left:130px;top:4065px;font-size:38px;font-weight:300;color:var(--ink)}
.contact h2 b{font-weight:800;color:var(--gold)}
.contact p{left:130px;width:345px;font-size:15.5px;line-height:27px;color:var(--text)}
.field{position:absolute;left:573px;width:512px;height:42px;border:1.5px solid #cfcfcf;background:var(--white);display:flex;align-items:center;gap:10px;padding-left:18px;font-size:13px;color:var(--muted)}
.field svg{flex:none}
.skyline{left:0;top:4380px;width:1200px;height:290px;background:linear-gradient(180deg,rgba(255,255,255,0) 0%,#ececec 60%,#d8d8d8 100%)}

/* footer */
.footer{left:0;top:4630px;width:1200px;height:387px;background:var(--footer);color:var(--white)}
.f-col{position:absolute;top:92px}
.f-col h4{font-size:19px;font-weight:600}
.f-col .u{width:75px;height:2px;background:var(--gold);margin:8px 0 14px}
.f-col li{list-style:none;font-size:12.5px;line-height:26px}
.f-contact{display:flex;align-items:center;gap:14px;margin-bottom:18px}
.f-contact .ic{width:28px;height:28px;border:1.5px solid #777;border-radius:50%;display:flex;align-items:center;justify-content:center}
.f-contact small{display:block;font-size:9px;color:#ccc}
.f-contact b{font-size:12px;font-weight:600}
.bottom{left:112px;top:4960px;width:976px;border-top:1px solid #333}
.bottom-text{top:4985px;font-size:13px;color:#ddd}
</style>
</head>
<body>

<!-- HERO -->
<section class="abs hero" role="img" aria-label="Construction site with tower crane and scaffolding at sunset"></section>
<div class="logo" style="left:112px;top:60px"><i class="mark"></i><span>KESTRADA</span></div>
<nav class="abs nav">
  <span class="active">HOME</span><span>ABOUT US</span><span>OUR SERVICES</span><span>PROJECTS</span><span>SDVOSB ADVANTAGE</span>
</nav>
<div class="btn" style="left:928px;top:38px;width:160px;height:46px">CONTACT US</div>
<div class="abs hero"><h1 class="abs" style="left:110px;top:185px">BUILDING VALUE.<b>DELIVERING<br>RESULTS.</b></h1>
<p class="abs">Kestrada is a trusted general contractor providing construction, disaster recovery, and environmental solutions to federal, state, and local clients.</p></div>
<div class="btn" style="left:110px;top:467px;width:243px;height:44px">DISCOVER PAYROLLING</div>
<div class="abs dots" style="left:111px;top:590px"><i></i><i></i><i class="on"></i></div>

<!-- ABOUT -->
<div class="abs about-photo" role="img" aria-label="Team meeting around a table in a bright office"></div>
<svg class="abs" style="left:0;top:600px" width="1200" height="200" viewBox="0 0 1200 200">
  <polygon points="0,14 780,176 1200,44 1200,0 0,0" fill="none"/>
  <polygon points="0,14 0,200 1200,200 1200,44 780,176" fill="#ffffff" opacity="0"/>
  <polygon points="0,12 780,170 1200,40 1200,60 780,190 0,40" fill="#ffffff" opacity=".0"/>
  <polygon points="460,100 780,176 1200,44 1200,60 780,186" fill="#d19a2a"/>
  <polygon points="0,14 780,176 1200,44 1200,200 0,200" fill="#ffffff" opacity=".0"/>
</svg>
<svg class="abs" style="left:0;top:610px" width="1200" height="170" viewBox="0 0 1200 170">
  <polygon points="0,0 780,150 1200,20 1200,28 780,160 0,30" fill="#ffffff" opacity=".85"/>
</svg>
<section class="about">
  <h2 class="abs">ABOUT <b>US</b></h2>
  <p class="abs" style="top:935px">Kestrada is a full-service general contracting firm specializing in high-quality construction and recovery solutions for government and institutional clients. As a <strong>Service-Disabled Veteran-Owned Small Business (SDVOSB)</strong>, we combine military precision, leadership, and discipline with industry expertise to deliver results that exceed expectations.</p>
  <p class="abs" style="top:1122px">Galoremque laudantium, totam rem aperiam, eaque ipsa quae ab illo inventore veritatis et quasi.</p>
  <div class="btn" style="left:612px;top:1204px;width:160px;height:44px">LEARN MORE</div>
</section>

<!-- SERVICES -->
<section class="abs services">
  <h2 class="sec-title" style="top:100px">OUR <b>SERVICES</b></h2>
  <div class="card" style="left:112px"><div class="ph" role="img" aria-label="Two engineers in hard hats and safety vests" style="background:linear-gradient(160deg,#c7a377,#e0b23f 60%,#7e8a55)"></div><h3>General Contracting</h3><p>Perspiciatis unde omnis iste natus error sit voluptatem accusantium doloremque laudantium totamre</p></div>
  <div class="card" style="left:360px"><div class="ph" role="img" aria-label="Modern timber and glass house" style="background:linear-gradient(160deg,#9fb6c4,#6b5a48 55%,#4d5b3a)"></div><h3>Design-Build Construction</h3><p>Perspiciatis unde omnis iste natus error sit voluptatem accusantium doloremque laudantium totamre</p></div>
  <div class="card hover" style="left:610px"><div class="ph" role="img" aria-label="Crew clearing storm debris in front of a damaged house" style="background:linear-gradient(160deg,#a9c1cf,#8a7458 55%,#c8b060)"></div><h3>Disaster Recovery</h3><p>Perspiciatis unde omnis iste natus error sit voluptatem accusantium doloremque laudantium totamre</p><div class="more"><span>LEARN MORE</span><svg width="30" height="10"><path d="M0 5H28M23 1L28 5L23 9" stroke="#c8923a" fill="none" stroke-width="1.2"/></svg></div></div>
  <div class="card" style="left:858px"><div class="ph" role="img" aria-label="Workers in protective suits at a remediation site" style="background:linear-gradient(160deg,#d6dbe0,#c9c47a 55%,#8c8a78)"></div><h3>Environmental Remediation</h3><p>Perspiciatis unde omnis iste natus error sit voluptatem accusantium doloremque laudantium totamre</p></div>
</section>

<!-- CLIENTS -->
<h2 class="sec-title" style="top:2180px">OUR <b style="color:var(--gold)">CLIENTS</b></h2>
<div class="rule" style="left:552px;top:2245px"></div>
<div class="client" style="left:60px"><div class="seal" style="left:75px;top:45px;width:132px;height:132px;background:#1f3e86"></div><div class="name">PMX</div></div>
<div class="divider" style="left:320px"></div>
<div class="client" style="left:322px"><div class="seal" style="left:107px;top:40px;width:68px;height:68px;background:#243a72"></div><div style="position:absolute;top:120px;width:100%;font-size:30px;font-weight:600;color:var(--ink)">TQ</div><div class="name">TQ</div></div>
<div class="divider" style="left:603px"></div>
<div class="client" style="left:613px"><div class="seal" style="left:72px;top:35px;width:52px;height:52px;background:#233c7a"></div><div class="seal" style="left:157px;top:35px;width:52px;height:52px;background:#233c7a"></div><div class="seal" style="left:72px;top:100px;width:52px;height:52px;background:#233c7a"></div><div class="seal" style="left:157px;top:100px;width:52px;height:52px;background:#1f4a2c"></div><div class="name">STATE AND LOCAL GOV'T AGENCIES</div></div>
<div class="divider" style="left:893px"></div>
<div class="client" style="left:860px"><div class="seal" style="left:80px;top:45px;width:125px;height:125px;background:#fff;border-color:#2b4a8c"></div><div class="name">HOSPITALS AND SCHOOLS</div></div>

<!-- EVENTS -->
<section class="abs events">
  <h2 class="sec-title" style="top:95px">OUR <b>EVENTS</b></h2>
  <div class="rule" style="left:552px;top:152px;background:#fff"></div>
  <div class="abs event-main" role="img" aria-label="Volunteers collecting litter on a beach">
    <div class="event-cap"><h3>Perspiciatis unde omnis istase</h3><p>Garspiciatis unde omnis istase naase seoitus error slksae icasit.</p></div>
  </div>
  <div class="event-sm" style="top:195px"><div class="ph" role="img" aria-label="Workers cleaning an industrial shoreline" style="background:linear-gradient(160deg,#8fb1cc,#b4a98c)"></div><div class="body"><span class="badge">14 JULY 2025</span><h4>Perspiciatis unde omnis istase ksaoeic uesechz</h4><p>Haoloremque laudan saecs secse seltium, totam aseem aperiam, eaque ipsa quae aseeb illo inventore.</p></div></div>
  <div class="event-sm" style="top:408px"><div class="ph" role="img" aria-label="Volunteers sorting donations outdoors" style="background:linear-gradient(160deg,#6c5a4c,#d4a33c 60%,#8e6a48)"></div><div class="body"><span class="badge">14 JULY 2025</span><h4>Perspiciatis unde omnis istase ksaoeic uesechz</h4><p>Haoloremque laudan saecs secse seltium, totam aseem aperiam, eaque ipsa quae aseeb illo inventore.</p></div></div>
  <div class="btn-outline">VIEW ALL</div>
</section>

<!-- TESTIMONIALS -->
<section class="abs testi">
  <h2 class="sec-title" style="top:85px"><b>TESTIMONIALS</b></h2>
  <div class="rule" style="left:552px;top:148px"></div>
  <div class="t-card" style="left:-40px;width:140px"><p style="position:absolute;right:16px;top:85px;font-size:12px;line-height:22px;font-style:italic;color:#666;text-align:right">saying<br>n to get<br>esign</p></div>
  <div class="t-card" style="left:1128px;width:140px"><p style="position:absolute;left:58px;top:85px;font-size:12px;line-height:22px;font-style:italic;color:#666">"I<br>so<br>t</p></div>
  <div class="t-card t-main" style="left:112px;width:978px">
    <span class="quote" style="left:115px;top:14px">“</span><span class="quote" style="right:95px;top:40px">”</span>
    <h3>Dorian Meltzer</h3><div class="role">Ksoiec, Iseoics</div>
    <p>"I perspiciatis unde omnis iste natus error sit voluptatem accusantium doloremque laudantium, totam rem aperiam, eaque ipsa quae ab illo inventore veritatis et quasi architecto beatae vitae dicta sunt explicabo. Nemo enim ipsam voluptatem quia voluptas sit aspernatur aut."</p>
  </div>
  <div class="abs dots" style="left:581px;top:432px"><i></i><i class="on"></i><i></i><i></i></div>
</section>

<!-- CONTACT -->
<div class="abs skyline" role="img" aria-label="Line sketch of a city skyline"></div>
<section class="contact">
  <h2 class="abs">CONTACT <b>US</b></h2>
  <div class="rule" style="left:130px;top:4128px"></div>
  <p class="abs" style="top:4158px">Gaerspiciatis unde omnis iste natus error sit voluptatem accusantium doloremque laudantium, totam rem aperiam, eaque ipsa quae ab illo inventore.</p>
  <p class="abs" style="top:4292px">Kasoeicnseoc omnis iste natus error sit voluptatem accusantium doloremque laudantium, totam rem aperiam, eaque ipsa quae ab illo inventore.</p>
  <div class="field" style="top:4063px"><svg width="12" height="12"><circle cx="6" cy="3.5" r="3" fill="#c8923a"/><path d="M0 12C0 8 12 8 12 12Z" fill="#c8923a"/></svg>Your Name *</div>
  <div class="field" style="top:4123px"><svg width="13" height="10"><rect width="13" height="10" rx="1" fill="#c8923a"/><path d="M0 1L6.5 6L13 1" stroke="#fff" fill="none"/></svg>Email *</div>
  <div class="field" style="top:4182px"><svg width="12" height="12"><path d="M2 0L5 3L3.5 5C4.5 7 5 7.5 7 8.5L9 7L12 10L10 12C5 12 0 7 0 2Z" fill="#c8923a"/></svg>Phone Number *</div>
  <div class="field" style="top:4242px;height:124px;align-items:flex-start;padding-top:14px"><svg width="12" height="12"><path d="M1 11L3 9L10 2L11 3L4 10Z" fill="#c8923a"/></svg>Enter Your Message *</div>
  <div class="btn" style="left:573px;top:4392px;width:183px;height:44px">SEND MESSAGE</div>
</section>

<!-- FOOTER -->
<svg class="abs" style="left:0;top:4470px" width="1200" height="170" viewBox="0 0 1200 170">
  <polygon points="0,170 380,40 820,40 1200,170" fill="#0b0b0b"/>
  <polygon points="0,165 380,32 820,32 1200,165 1200,172 820,42 380,42 0,172" fill="#d19a2a"/>
</svg>
<footer class="abs footer">
  <div class="logo" style="left:175px;top:120px"><i class="mark"></i><span>KESTRADA</span></div>
  <div class="abs" style="left:207px;top:190px;width:30px;height:30px;border:1.5px solid #fff;border-radius:50%"></div>
  <div class="abs" style="left:247px;top:190px;width:30px;height:30px;background:var(--gold);border-radius:50%"></div>
  <div class="f-col" style="left:433px"><h4>Quick links</h4><div class="u"></div><ul><li>Home</li><li>About Us</li><li>Our Services</li><li>Projects</li><li>SDVOSB Advantage</li><li>Contact Us</li></ul></div>
  <div class="f-col" style="left:630px"><h4>Links</h4><div class="u"></div><ul><li>Copyright</li><li>Legal</li><li>Privacy</li><li>Accessibility</li><li>Sitemap</li></ul></div>
  <div class="f-col" style="left:783px"><h4>Contact Us</h4><div class="u"></div>
    <div class="f-contact"><span class="ic"><svg width="12" height="12"><path d="M2 0L5 3L3.5 5C4.5 7 5 7.5 7 8.5L9 7L12 10L10 12C5 12 0 7 0 2Z" fill="#fff"/></svg></span><div><small>Call Us</small><b>+1 555.010.0199</b></div></div>
    <div class="f-contact"><span class="ic"><svg width="12" height="9"><rect width="12" height="9" rx="1" fill="#fff"/><path d="M0 1L6 5L12 1" stroke="#000" fill="none"/></svg></span><div><small>Email</small><b>info@kestrada.com</b></div></div>
    <div class="f-contact"><span class="ic"><svg width="10" height="13"><path d="M5 13C5 13 0 7 0 5A5 5 0 0 1 10 5C10 7 5 13 5 13Z" fill="#fff"/><circle cx="5" cy="5" r="2" fill="#000"/></svg></span><div><small>Address</small><b>4120 Marlow Lane, Denver, CO 80202</b></div></div>
  </div>
  <div class="abs" style="left:1125px;top:280px;width:40px;height:40px;border:1.5px solid #888;border-radius:8px;display:flex;align-items:center;justify-content:center"><svg width="12" height="8"><path d="M1 7L6 2L11 7" stroke="#fff" fill="none" stroke-width="1.5"/></svg></div>
</footer>
<div class="abs bottom"></div>
<div class="abs bottom-text" style="left:112px">© 2025. All rights reserved.</div>
<div class="abs bottom-text" style="left:868px">Terms of use</div>
<div class="abs bottom-text" style="left:995px">Privacy Policy</div>

</body>
</html>
```